Web Design job: SaaS start-up needs a cutting-edge web design

What's Needed:
- All designs files created
- Fully coded implementation in HTML/CSS/Bootstrap
- Pages: 5 -- see content here http://www.TeamVerdexa.com
-- Home Page
-- The Hidden Value
-- Benefits
-- About us
-- Careers
- The existing site has the textual content for each page. We can tweak to meet specific designs if needed.
- You will need to update/create image and interactive content for pages.

Reference:
Our existing website has a lot of content on it for reference -
http://www.TeamVerdexa.com

Description:
We need a web design that focuses in the UX and conveys the idea of magically fixing company problems by way of using our software.

Home Page
The main goal is to Drive Sales of the SaaS tool. When a visitor lands on our home page they should see: What we do, How we can help their problem and How to contact us.
1. Quickly understand What We Do
-- we sell SaaS software.
-- Need to quickly convey what our software does. It's seems complicated but really its not. See the description in about us for more info and visit our existing site.

2. How we can help their problem
-- We aim to solve any problem related to employees
-- Even if the visitor does not have a specific problem in mind, there are several areas organizations can always improve: (some examples below)
---- Create Stronger, More Productive Teams
---- Build Better Communications Pathways
---- Encourage Innovation and Positive Change
---- Develop and Retain Strong "Company Culture"

3. Be able to Contact Us to get started
-- contacting us to get a sales lead is the ultimate goal.
-- the user should not have to hunt to contact us. needs to be easy.

Other Pages (Hidden Value, Benefit, About Us, Careers):
-- These are informative pages about our software and process.
-- If we grab the attention of the user on the home page then these are the pages that they will explore for more info.
-- Should be able to link to these pages from the main nav or from sections with the homepage. For example: What We Do sections could link to the benefits page. How we help their problem sections could link to the Hidden Value page. Regardless of what links to where, the idea is that we will be able to nav to other areas.

About Us:
Our company name is TeamVerdexa (as in Organizational Analysis). We provide a software as a service (SaaS) that uses a simple 6-question survey to analyze the relationships of people within an Organization and provide leaders with ground-breaking Insights about their teams, interactive social network data visualizations to explore their team's composition and we give detailed profiles of the key players (i.e, who are the Social Bridges, Who are the Knowledge Bottlenecks, Who are the Best Mentors, Who are the people that are completely disconnected/out of the loop). Leaders then use this information to make high level organizational decisions.

What's unique about our software:
-- Powerful analysis results from just a 6-question "pulse-surveys"
-- Innovative Tools for visually exploring the organization through relationships as opposed to org-chart
-- Get real-time results as opposed to waiting months with traditional methods
-- Traditional Org-charts represent the organization's skeleton, whereas we uncover the organization's neural network (how it solves problems).

Preferred fonts (but could be convinced otherwise if looks great):
-- Section titles - Aleo
-- Main body - Lato
-- TeamVerdexa logo - Philosopher

Things we like:
-- We like a big slider as the top of the landing page.

Colors to include:
-- Colors in the logo (red, blue, green, teal) as accent colors

Feel of the site:
-- Cutting-edge Software
-- Professional
-- Social Network flare (we analyze relationships)

Note:
If we find a great match with a designer there is strong possibility to continue the relationship with follow on work redesigning our web-based application.

Target Market(s)

Current customers are Morrow Pike & Fenwell, Clearbrook Valley Bank.
We target anyone that manages a large team. Such as Corporate Leaders, High Level Managers, HR Leaders

Industry/Entity Type

Business Software

Contact Information for Business Card

Logo image
Name of company "TEAMVERDEXA" In Philosopher font.
Tagline: "Unlock the Hidden Value In Your Teams"
Person's Name, Title, email, phone.

Coding

Coded - Design and coding required

Number of Pages Required

4 page

Font styles to use
Other font styles liked:
• Lato, Philosopher, Aero

Colors
ec1f27
0255a3

Requirements
Must have
• See description.
Nice to have
• Things we like:
• We like a big slider as the top of the landing page. Ours is a little clunky and outdated but something fresh and sleek would be great.
• Colors to include:
• We would like to use the colors in the logo as accent colors in the site to give a consistent look and feel.
• Feel of the site:
• Cutting-edge Software
• Professional
• Social Network flare (we analyze relationships)

```html
<!DOCTYPE html>
<html lang="en">
<head>
<meta charset="utf-8">
<title>TeamVerdexa</title>
<link rel="stylesheet" href="https://fonts.googleapis.com/css2?family=Aleo:wght@400;700&family=Lato:wght@400;700&display=swap">
<style>
:root{
  --red:#e52a2f;
  --blue:#0d4f9e;
  --navy:#2f3a8f;
  --ink:#333;
  --muted:#777;
  --grey-band:#ececec;
  --line:#dcdcdc;
  --dark-btn:#3a3a3a;
}
*{box-sizing:border-box;margin:0;padding:0}
html,body{width:686px;height:1200px;overflow:hidden;background:#fff}
body{position:relative;font-family:"Lato",sans-serif;color:var(--ink)}
.abs{position:absolute}
.serif{font-family:"Aleo",serif}

.site-header{left:0;top:0;width:686px;height:99px}
.brand{left:75px;top:22px;width:130px;height:64px;display:flex;flex-direction:column;align-items:center;justify-content:flex-end}
.brand-dot{width:30px;height:30px;border-radius:50%;background:var(--red);margin-bottom:8px}
.brand-name{font-family:"Lato",sans-serif;font-weight:700;font-size:13.5px;color:var(--navy);letter-spacing:.5px;white-space:nowrap}
.client-login{left:545px;top:28px;width:65px;height:24px;border:1px solid #ccc;font-size:7px;display:flex;align-items:center;justify-content:center;gap:4px;color:#333}
.main-nav{left:352px;top:72px;display:flex;gap:16px;font-family:"Aleo",serif;font-size:8.6px;color:#222}
.main-nav .active{color:var(--red);position:relative}
.main-nav .active svg{position:absolute;left:7px;top:-8px}

.hero{left:0;top:99px;width:686px;height:251px;background:linear-gradient(100deg,#7d8c98 0%,#c9ced2 35%,#e9eaea 60%,#b9bfc4 100%)}
.hero-title{left:0;top:134px;width:686px;text-align:center;font-size:16.5px;color:#333}
.hero-arrow{top:216px;width:14px;height:18px;background:#777;display:flex;align-items:center;justify-content:center}

.welcome-title{left:0;top:375px;width:686px;text-align:center;font-size:17px;font-weight:700;color:var(--blue)}
.welcome-text{left:75px;top:400px;width:535px;font-size:6.9px;line-height:12.5px;color:#555;text-align:center}
.welcome-text strong{font-weight:400;color:#111;font-size:7.4px}

.unique{left:0;top:478px;width:686px;height:237px;background:var(--grey-band)}
.unique-title{left:0;top:501px;width:686px;text-align:center;font-size:16px;color:var(--red)}
.u-item{font-size:8.6px;line-height:12px;color:var(--blue);width:160px}
.u-left{text-align:justify}
.u-right{text-align:right}
.u-icon{position:absolute}
.laptop{left:244px;top:562px;width:198px;height:122px}
.laptop-screen{position:absolute;left:26px;top:0;width:146px;height:110px;background:#111;border:3px solid #2b2b2b;border-radius:5px 5px 0 0}
.laptop-base{position:absolute;left:4px;top:108px;width:190px;height:10px;background:linear-gradient(#e8e8e8,#bdbdbd);border-radius:0 0 10px 10px}

.feat{width:240px}
.feat h3{font-family:"Lato",sans-serif;font-weight:400;font-size:11px;color:var(--red);margin-bottom:3px}
.feat p{font-size:6.6px;line-height:9px;color:#777;width:205px}
.feat-icon{position:absolute;left:-30px;top:0}

.map{left:0;top:948px;width:342px;height:141px;background:linear-gradient(#dadada,#e6e6e6)}
.contact{left:342px;top:948px;width:344px;height:141px;background:var(--grey-band)}
.contact-title{left:370px;top:960px;font-size:16px;color:#333}
.field{width:104px;height:20px;background:#fff;font-size:7px;color:#777;padding:6px 10px}
.submit{background:var(--dark-btn);color:#fff;text-align:center;font-size:7px;padding-top:6px}

.office{font-size:6.6px;color:#555;line-height:12px}
.office b{font-weight:400;font-size:7.4px;color:#333}
.office svg{vertical-align:-1px;margin-right:3px}
.footer-rule{left:75px;top:1153px;width:535px;height:1px;background:var(--line)}
.footer-links{left:75px;top:1164px;font-size:6px;color:#333}
.footer-links span{margin:0 3px;color:#999}
.copyright{left:75px;top:1179px;font-size:6px;color:#333}
.social{top:1168px;width:15px;height:15px;border-radius:50%}
</style>
</head>
<body>

<header class="abs site-header">
  <div class="abs brand"><div class="brand-dot"></div><div class="brand-name">TEAM VERDEXA</div></div>
  <div class="abs client-login">
    <svg width="6" height="7" viewBox="0 0 6 7"><rect x="0.5" y="3" width="5" height="4" fill="#333"/><path d="M1.5 3V2a1.5 1.5 0 0 1 3 0v1" stroke="#333" fill="none"/></svg>
    Client Login
  </div>
  <nav class="abs main-nav">
    <span class="active"><svg width="8" height="7" viewBox="0 0 8 7"><path d="M4 0L0 3.5h1V7h2.2V5h1.6v2H7V3.5h1z" fill="#e52a2f"/></svg>Home</span>
    <span>The Hidden Value</span><span>Benefits</span><span>About Us</span><span>Careers</span>
  </nav>
</header>

<section class="abs hero" role="img" aria-label="Photo of hands typing on a laptop keyboard at a desk"></section>
<h1 class="abs hero-title serif" style="font-weight:400">We provide a software as a service (SaaS)</h1>
<div class="abs hero-arrow" style="left:0"><svg width="6" height="10"><path d="M5 1L1 5l4 4" stroke="#fff" fill="none"/></svg></div>
<div class="abs hero-arrow" style="left:672px"><svg width="6" height="10"><path d="M1 1l4 4-4 4" stroke="#fff" fill="none"/></svg></div>

<h2 class="abs welcome-title serif">Welcome</h2>
<p class="abs welcome-text">Our company name is TeamVerdexa (as in Organizational Analysis). We provide a software as a service (SaaS) that uses a simple 6-question survey to analyze the relationships of people within an Organization and provide leaders with ground-breaking Insights about their teams, interactive social network data visualizations to explore their team's composition and we give detailed profiles of the key players <strong>(i.e, who are the Social Bridges, Who are the Knowledge Bottlenecks, Who are the Best Mentors, Who are the people that are completely disconnected/out of the loop)</strong>. Leaders then use this information to make high level organizational decisions.</p>

<section class="abs unique"></section>
<h2 class="abs unique-title serif" style="font-weight:400">What's unique about our software</h2>

<svg class="u-icon" style="left:143px;top:526px" width="24" height="20" viewBox="0 0 24 20"><rect x="1" y="3" width="16" height="15" rx="2" fill="none" stroke="#0d4f9e" stroke-width="2"/><path d="M8 13l1-4 9-8 3 3-9 8z" fill="#0d4f9e"/></svg>
<p class="abs u-item u-left" style="left:75px;top:553px">Powerful analysis results from just a 6-question "pulse-surveys"</p>

<svg class="u-icon" style="left:516px;top:524px" width="26" height="24" viewBox="0 0 26 24"><circle cx="10" cy="14" r="6" fill="none" stroke="#0d4f9e" stroke-width="4" stroke-dasharray="3 2"/><circle cx="20" cy="6" r="4" fill="none" stroke="#0d4f9e" stroke-width="3" stroke-dasharray="2 1.5"/><circle cx="21" cy="18" r="3.5" fill="none" stroke="#0d4f9e" stroke-width="3" stroke-dasharray="2 1.5"/></svg>
<p class="abs u-item u-right" style="left:450px;top:553px">Get real-time results as opposed to waiting months with traditional methods</p>

<svg class="u-icon" style="left:144px;top:608px" width="22" height="22" viewBox="0 0 22 22"><path d="M2 20l10-10" stroke="#0d4f9e" stroke-width="4" stroke-linecap="round"/><circle cx="15" cy="7" r="5" fill="#0d4f9e"/><circle cx="17" cy="5" r="2.5" fill="#ececec"/></svg>
<p class="abs u-item u-left" style="left:75px;top:635px">Innovative Tools for visually exploring the organization through relationships as opposed to org-chart</p>

<svg class="u-icon" style="left:518px;top:608px" width="24" height="20" viewBox="0 0 24 20"><rect x="9" y="1" width="6" height="5" fill="#0d4f9e"/><rect x="1" y="14" width="6" height="5" fill="#0d4f9e"/><rect x="9" y="14" width="6" height="5" fill="#0d4f9e"/><rect x="17" y="14" width="6" height="5" fill="#0d4f9e"/><path d="M12 6v8M4 14v-4h16v4" stroke="#0d4f9e" stroke-width="1.5" fill="none"/></svg>
<p class="abs u-item u-right" style="left:450px;top:635px">Traditional Org-charts represent the organization's skeleton, whereas we uncover the organization's neural network (how it solves problems).</p>

<div class="abs laptop" role="img" aria-label="Laptop showing the product splash screen">
  <div class="laptop-screen"></div>
  <div class="laptop-base"></div>
</div>

<div class="abs feat" style="left:106px;top:755px">
  <svg class="feat-icon" width="22" height="18" viewBox="0 0 22 18"><path d="M1 1v16h20" stroke="#e52a2f" stroke-width="2" fill="none"/><path d="M3 14l5-6 4 3 7-8" stroke="#e52a2f" stroke-width="2" fill="none"/></svg>
  <h3>Impact on Business Results</h3><p>Optimize organizations to fill communication gaps and mitigate risks to success</p>
</div>
<div class="abs feat" style="left:401px;top:755px">
  <svg class="feat-icon" width="22" height="18" viewBox="0 0 22 18"><circle cx="6" cy="5" r="3" fill="#e52a2f"/><circle cx="16" cy="5" r="3" fill="#e52a2f"/><circle cx="11" cy="8" r="3.5" fill="#e52a2f"/><path d="M1 15a5 5 0 0 1 10-4 5 5 0 0 1 10 4v2H1z" fill="#e52a2f"/></svg>
  <h3>Identify Key Team Members</h3><p>Understand roles that individuals play within the team beyond their titles</p>
</div>
<div class="abs feat" style="left:106px;top:815px">
  <svg class="feat-icon" width="18" height="18" viewBox="0 0 18 18"><circle cx="9" cy="9" r="8" fill="#e52a2f"/><path d="M5 5c2 0 3 2 2 4s1 3 3 3M11 3c1 2 3 2 4 3" stroke="#fff" stroke-width="1.6" fill="none"/></svg>
  <h3>Real World Applications</h3><p>Leverage an underutilized Asset to drive company performance</p>
</div>
<div class="abs feat" style="left:401px;top:815px">
  <svg class="feat-icon" width="20" height="16" viewBox="0 0 20 16"><g fill="#e52a2f"><rect x="0" y="1" width="3" height="3"/><rect x="0" y="6.5" width="3" height="3"/><rect x="0" y="12" width="3" height="3"/><rect x="5" y="1" width="15" height="3"/><rect x="5" y="6.5" width="15" height="3"/><rect x="5" y="12" width="15" height="3"/></g></svg>
  <h3>Simple Data Collection</h3><p>Powerful results from fast 6-question survey</p>
</div>
<div class="abs feat" style="left:106px;top:874px">
  <svg class="feat-icon" width="18" height="18" viewBox="0 0 18 18"><g fill="#e52a2f"><circle cx="4" cy="9" r="3.5"/><circle cx="14" cy="3.5" r="3.5"/><circle cx="14" cy="14.5" r="3.5"/></g><path d="M4 9l10-5.5M4 9l10 5.5" stroke="#e52a2f" stroke-width="2"/></svg>
  <h3>Automated Exploration Tools</h3><p>Real-time network visualizations, gap analysis, metrics, scorecards, findings and recommendations</p>
</div>
<div class="abs feat" style="left:401px;top:874px">
  <svg class="feat-icon" width="22" height="16" viewBox="0 0 22 16"><path d="M5 15a4.5 4.5 0 0 1-.5-9A6 6 0 0 1 16 5a5 5 0 0 1 1 10z" fill="#e52a2f"/></svg>
  <h3>SaaS Architecture</h3><p>24/7 access, secure &amp; encrypted connection and free feature updates</p>
</div>

<div class="abs map" role="img" aria-label="Grey world map showing office locations"></div>
<section class="abs contact"></section>
<h2 class="abs contact-title serif" style="font-weight:400">Contact Us</h2>
<div class="abs field" style="left:371px;top:988px">Name</div>
<div class="abs field" style="left:481px;top:988px">Phone</div>
<div class="abs field" style="left:371px;top:1015px">Email</div>
<div class="abs field" style="left:481px;top:1015px">Company name</div>
<div class="abs field" style="left:371px;top:1043px">Message</div>
<div class="abs field submit" style="left:481px;top:1043px">SUBMIT</div>

<div class="abs office" style="left:75px;top:1101px"><b>Maplecrest, OH</b><br><svg width="4" height="6"><rect width="4" height="6" rx="1" fill="#555"/></svg>513-555-0142<br><svg width="6" height="5"><rect width="6" height="5" fill="#555"/></svg>maplecrest@teamverdexa.com</div>
<div class="abs office" style="left:222px;top:1101px"><b>Ridgeford, CO</b><br><svg width="4" height="6"><rect width="4" height="6" rx="1" fill="#555"/></svg>720-555-0186<br><svg width="6" height="5"><rect width="6" height="5" fill="#555"/></svg>ridgeford@teamverdexa.com</div>
<div class="abs office" style="left:372px;top:1101px"><b>Harlow Springs, AL</b><br><svg width="4" height="6"><rect width="4" height="6" rx="1" fill="#555"/></svg>205-555-0173<br><svg width="6" height="5"><rect width="6" height="5" fill="#555"/></svg>harlow@teamverdexa.com</div>
<div class="abs office" style="left:530px;top:1101px"><b>Lakemont, IL</b><br><svg width="4" height="6"><rect width="4" height="6" rx="1" fill="#555"/></svg>720-555-0186<br><svg width="6" height="5"><rect width="6" height="5" fill="#555"/></svg>lakemont@teamverdexa.com</div>

<div class="abs footer-rule"></div>
<p class="abs footer-links">Home<span>|</span>The Hidden Value<span>|</span>Benefits<span>|</span>About Us<span>|</span>Careers</p>
<p class="abs copyright">Copyright © 2016 Company name. All rights reserved.</p>
<div class="abs social" style="left:557px;background:#2f4f8f"></div>
<div class="abs social" style="left:576px;background:#1d8fd6"></div>
<div class="abs social" style="left:595px;background:#1b6fa8"></div>

</body>
</html>
```